Animal Eye Clinic needs a Business card

We are a new veterinary ophthalmology practice (Ridgeline Pet Vision Care) and we need a business card designed. We only see animal eyes - we are not a regular veterinary clinic. We already have a logo. We are looking for a professional, good looking business card to hand out to our clients. We are looking for something simple but professional and contemporary. Our logo is likely the only picture/graphic that needs to be on the card.
Updates

Contact Information for Business Card

Delia Vossman, BSc, DVM, MSc, DipACVO
Veterinary Ophthalmologist

Phone: 250.418.3927
Email: ridgelinepetvisioncare@mailbox-example.net
Website: ridgelinepetvisioncare-example.net
Address: 1874 Thornbury Rd
Kelowna, BC, V1X 4M9

Colors

Designer to choose colors to be used in the design.

Requirements
Must have
• Our logo (attached)

```html
<!DOCTYPE html>
<html lang="en">
<head>
<meta charset="utf-8">
<title>Ridgeline Pet Vision Care – Business Card</title>
<link rel="stylesheet" href="https://fonts.googleapis.com/css2?family=Roboto:wght@400;500;700&display=swap">
<style>
  :root {
    --teal: #1a94a3;
    --teal-deep: #16838f;
    --grey-text: #6b6b6b;
    --slate: #6e6e6e;
    --white: #ffffff;
    --stage: #e9ebed;
    --card-shadow: 0 6px 18px rgba(0,0,0,.18);
  }
  * { box-sizing: border-box; margin: 0; padding: 0; }
  html, body { width: 1200px; height: 800px; overflow: hidden; }
  body {
    background: var(--stage);
    font-family: "Roboto", Arial, sans-serif;
    position: relative;
  }
  .card {
    position: absolute;
    width: 630px;
    height: 360px;
    box-shadow: var(--card-shadow);
    overflow: hidden;
  }

  /* Front side */
  .card-front {
    left: 420px;
    top: 24px;
    background: var(--white);
  }
  .brand {
    position: absolute;
    left: 0; right: 0;
    top: 130px;
    display: flex;
    align-items: center;
    justify-content: center;
    gap: 16px;
  }
  .brand-dot {
    width: 46px; height: 46px;
    border-radius: 50%;
    background: var(--teal);
    flex: none;
  }
  .brand-name {
    color: var(--teal);
    font-weight: 700;
    font-size: 30px;
    letter-spacing: .5px;
    text-transform: uppercase;
  }
  .front-url {
    position: absolute;
    left: 0; right: 0;
    top: 250px;
    text-align: center;
    color: var(--grey-text);
    font-size: 15px;
    letter-spacing: 2.4px;
  }

  /* Back side */
  .card-back {
    left: 150px;
    top: 416px;
    background: var(--teal);
    color: var(--white);
  }
  .back-art {
    position: absolute;
    right: 0; top: 90px;
    width: 190px; height: 270px;
    background: linear-gradient(160deg, #ffffff 0%, #f1f3f4 100%);
    border-top-left-radius: 110px;
  }
  .contact {
    position: absolute;
    left: 42px; top: 42px;
    z-index: 1;
  }
  .person-name {
    font-size: 22px;
    font-weight: 700;
    letter-spacing: .3px;
    text-transform: uppercase;
    white-space: nowrap;
  }
  .person-name .credentials {
    font-size: 14px;
    text-transform: none;
    margin-left: 4px;
  }
  .person-title {
    font-size: 17px;
    margin-top: 2px;
  }
  .address {
    font-size: 17px;
    line-height: 1.3;
    margin-top: 38px;
    font-style: normal;
  }
  .channels {
    list-style: none;
    margin-top: 14px;
    font-size: 16px;
    line-height: 1.45;
  }
  .channels li {
    display: flex;
    align-items: center;
    gap: 7px;
    white-space: nowrap;
  }
  .channels svg { width: 14px; height: 14px; flex: none; }
</style>
</head>
<body>

<section class="card card-front" aria-label="Card front">
  <div class="brand">
    <span class="brand-dot"></span>
    <span class="brand-name">Ridgeline Pet Vision Care</span>
  </div>
  <p class="front-url">ridgelinepetvisioncare-example.net</p>
</section>

<section class="card card-back" aria-label="Card back">
  <div class="back-art" role="img" aria-label="Silhouettes of a horse, a dog and a cat in teal, white and grey"></div>
  <div class="contact">
    <h1 class="person-name">Delia Vossman <span class="credentials">BSc, DVM, MSc, DipACVO</span></h1>
    <p class="person-title">Veterinary Ophthalmologist</p>
    <address class="address">1874 Thornbury Rd<br>Kelowna, BC, V1X 4M9</address>
    <ul class="channels">
      <li>
        <svg viewBox="0 0 24 24" aria-hidden="true"><path fill="#fff" d="M6.6 10.8a15.1 15.1 0 0 0 6.6 6.6l2.2-2.2c.3-.3.7-.4 1-.2 1.1.4 2.3.6 3.6.6.6 0 1 .4 1 1V20c0 .6-.4 1-1 1A17 17 0 0 1 3 4c0-.6.4-1 1-1h3.5c.6 0 1 .4 1 1 0 1.3.2 2.5.6 3.6.1.3 0 .7-.2 1z"/></svg>
        250.418.3927
      </li>
      <li>
        <svg viewBox="0 0 24 24" aria-hidden="true"><rect x="2.5" y="5" width="19" height="14" fill="none" stroke="#fff" stroke-width="2"/><path d="M3 6l9 7 9-7" fill="none" stroke="#fff" stroke-width="2"/></svg>
        ridgelinepetvisioncare@mailbox-example.net
      </li>
      <li>
        <svg viewBox="0 0 24 24" aria-hidden="true"><g fill="none" stroke="#fff" stroke-width="1.8"><circle cx="12" cy="12" r="9.5"/><ellipse cx="12" cy="12" rx="4" ry="9.5"/><path d="M2.5 12h19M4 7h16M4 17h16"/></g></svg>
        ridgelinepetvisioncare-example.net
      </li>
    </ul>
  </div>
</section>

</body>
</html>
```